Business Card for beauty technology startup

Design Glimora Business Card for a Beauty, based on the website identity and colors (https://www.glimora-example.com).
Glimora is a beauty tech startup that gathers helpful product info for beauty lovers and consumers (such as availability on stores, price range and product reviews) for makeup products. The card design must be young, colorful but clean, and very modern.

Target Market(s)

woman, 15-35

Industry/Entity Type

Cosmetics

Contact Information for Business Card

Full Name, address, phone

Font styles to use
Other font styles liked:
• Advent Pro

Colors
e34297
86cfc6
ffffff
5c5c5c
e8e8e8
e667a6
b2b2b2

Requirements
Must have
• One full colored side with a creative design and another with card info
• Use Color palette: #95C5C5 and/or #D38AA5
• Use fonts: Advent Pro
• Use website identity: https://www.glimora-example.com
Nice to have
• If needed extra font: Roboto

```html
<!DOCTYPE html>
<html lang="en">
<head>
<meta charset="utf-8">
<title>Glimora Business Card</title>
<link rel="stylesheet" href="https://fonts.googleapis.com/css2?family=Advent+Pro:wght@300;400;600&family=Roboto:wght@400&display=swap">
<style>
  :root {
    --page-bg: #e8e8e8;
    --card-front: #c97e99;
    --card-front-dark: #bd7189;
    --card-white: #fbfbf9;
    --brand-pink: #b9708b;
    --band-pink: #c67a93;
    --brand-teal: #7fafb3;
    --ink-dark: #2e2b2d;
    --ink-soft: #3d3d3d;
  }
  * { box-sizing: border-box; margin: 0; padding: 0; }
  html, body {
    width: 1200px;
    height: 576px;
    overflow: hidden;
    background: var(--page-bg);
  }
  .canvas {
    position: relative;
    width: 1200px;
    height: 576px;
  }
  .card {
    position: absolute;
    top: 138px;
    width: 484px;
    height: 293px;
    border-radius: 14px;
    overflow: hidden;
    box-shadow: 0 2px 6px rgba(0,0,0,0.18);
  }

  /* Front side */
  .card-front {
    left: 82px;
    background: linear-gradient(180deg, var(--card-front) 0%, var(--card-front-dark) 100%);
  }
  .front-brand {
    position: absolute;
    left: 106px;
    top: 115px;
    display: flex;
    align-items: center;
    gap: 22px;
  }
  .brand-dot {
    width: 62px;
    height: 62px;
    border-radius: 50%;
    border: 2px solid var(--ink-dark);
  }
  .front-brand .brand-name {
    font-family: "Advent Pro", sans-serif;
    font-weight: 300;
    font-size: 46px;
    letter-spacing: 5px;
    color: var(--ink-dark);
    line-height: 1;
  }

  /* Back side */
  .card-back {
    left: 602px;
    width: 481px;
    height: 292px;
    background: var(--card-white);
  }
  .back-brand {
    position: absolute;
    left: 26px;
    top: 36px;
    display: flex;
    align-items: center;
    gap: 24px;
  }
  .back-brand .brand-dot {
    width: 62px;
    height: 62px;
    border-color: var(--brand-pink);
  }
  .back-brand .brand-name {
    font-family: "Advent Pro", sans-serif;
    font-weight: 300;
    font-size: 42px;
    letter-spacing: 5px;
    color: var(--brand-pink);
    line-height: 1;
  }
  .holder-name {
    position: absolute;
    left: 24px;
    top: 164px;
    font-family: "Advent Pro", sans-serif;
    font-weight: 600;
    font-size: 22px;
    letter-spacing: 0.5px;
    color: var(--brand-teal);
  }
  .contact {
    position: absolute;
    left: 256px;
    top: 165px;
    font-family: "Roboto", sans-serif;
    font-size: 12px;
    color: var(--brand-pink);
    line-height: 16px;
  }
  .contact-address { margin-bottom: 13px; }
  .contact-line {
    display: flex;
    align-items: center;
    gap: 8px;
    margin-left: -16px;
  }
  .contact-line svg { width: 10px; height: 10px; flex: none; }
  .card-bands {
    position: absolute;
    left: 0;
    top: 0;
    width: 481px;
    height: 292px;
  }
  .website {
    position: absolute;
    left: 256px;
    top: 267px;
    font-family: "Roboto", sans-serif;
    font-size: 11.5px;
    color: var(--ink-soft);
  }
</style>
</head>
<body>
<main class="canvas">
  <section class="card card-front" aria-label="Card front">
    <div class="front-brand">
      <span class="brand-dot" aria-hidden="true"></span>
      <span class="brand-name">GLIMORA</span>
    </div>
  </section>

  <section class="card card-back" aria-label="Card back">
    <svg class="card-bands" viewBox="0 0 481 292" aria-hidden="true">
      <rect x="0" y="276" width="210" height="16" fill="var(--band-pink)"/>
      <polygon points="215,256 481,256 481,292 200,292" fill="var(--brand-teal)"/>
    </svg>
    <div class="back-brand">
      <span class="brand-dot" aria-hidden="true"></span>
      <span class="brand-name">GLIMORA</span>
    </div>
    <h1 class="holder-name">MARA ELLISON</h1>
    <div class="contact">
      <p class="contact-address">123, Street Number, City Name,<br>Country - 123456</p>
      <p class="contact-line">
        <svg viewBox="0 0 10 10" aria-hidden="true"><path d="M2 1 L3.6 1 L4.2 3 L3.1 3.8 Q4 5.9 6.2 6.9 L7 5.8 L9 6.4 L9 8 Q8.6 9 7.5 9 Q1 8 1 2.5 Q1 1 2 1 Z" fill="none" stroke="var(--brand-teal)" stroke-width="0.9"/></svg>
        <span>00 111 222 333</span>
      </p>
      <p class="contact-line">
        <svg viewBox="0 0 10 10" aria-hidden="true"><rect x="0.8" y="2" width="8.4" height="6" fill="none" stroke="var(--brand-teal)" stroke-width="0.9"/><path d="M0.8 2 L5 5.5 L9.2 2" fill="none" stroke="var(--brand-teal)" stroke-width="0.9"/></svg>
        <span>yourname@glimora-example.com</span>
      </p>
    </div>
    <p class="website">www.glimora-example.com</p>
  </section>
</main>
</body>
</html>
```